Ridge Lass Crew (Flyer)

I want a flyer to advertise my service.
Details below, and logo's to use are attached.

A girls only after school program, 11-14yrs, as OSHC is no longer avail, dedicated to coaching & mentoring our girls into strong, independent young women.

The Brainchild of Rebecca Folwin, Ridge Lass Crew was created to address the growing demand for after school/school holiday supervision for kids moving from primary into high school, when OSHC ceases to exist.
With over 12 years experience mentoring and coaching young women in the corporate world, Bec decided to leave her role as a Director with Tarrant Trust, and follow her passion.
Bec, along with her sister Lorraine, who has over 10 years experience in local communities as a Youth Worker, and is also a qualified Enrolled Nurse, embarked on building a program designed to keep parents happy (by knowing their girls are safe) and dedicated to coaching and mentoring our girls into strong, independent young women.
Open every afternoon and during school holidays, we look to offer;
- Daily meditation
- Healthy snacks
- Dedicated homework time
- Organised group activity, led by qualified instructors (yoga, fitness class, soccer etc)
- Regular guests speakers, addressing issues/concerns for young people today
- SOCIAL MEDIA FREE ZONE

Located 87 Pelham Pde, Larkfield Vale (across from Crestmoor Day Clinic)
Open 3-6pm Monday to Friday

Facebook page: http://fb.example/ridgelasscrew
Email: info@ridgelasscrew.example.au
Mobile: 0455817396

Target Market(s)

Parents of teenage girls, teenage girls 11-14 years

Industry/Entity Type

School

Font styles to use
Sans Serif

Colors
b768aa
e667a6

Requirements
Must have
• What progam is - see brief
• Who runs it
Should not have
• Not be too busy, not overly mature images

```html
<!DOCTYPE html>
<html lang="en">
<head>
<meta charset="utf-8">
<title>Ridge Lass Crew – After School Program Flyer</title>
<link rel="stylesheet" href="https://fonts.googleapis.com/css2?family=Cinzel:wght@600&family=Fira+Sans:wght@500;600&family=Fira+Sans+Condensed:wght@600&family=Chakra+Petch:wght@600;700&family=Montserrat:wght@700&display=swap">
<style>
  :root{
    --purple:#b768aa;
    --purple-deep:#9d5494;
    --pink:#e667a6;
    --ink:#2a1626;
    --white:#ffffff;
    --soft-white:#f6e8f0;
    --paper:#f7f2f5;
  }
  *{margin:0;padding:0;box-sizing:border-box}
  html,body{width:848px;height:1200px;overflow:hidden;background:var(--paper)}
  .flyer{position:relative;width:848px;height:1200px;overflow:hidden;background:var(--pink);font-family:"Fira Sans",sans-serif}

  .header-band{position:absolute;left:0;top:0;width:848px;height:188px;background:var(--purple)}
  .header-accent{position:absolute;left:0;top:0}

  .hero-photo{position:absolute;left:0;top:188px;width:848px;height:452px;
    background:linear-gradient(100deg,#dcd6d4 0%,#c9c2c0 30%,#e9e4e2 60%,#d3cdcb 100%)}

  .brand-tile{position:absolute;left:29px;top:20px;width:257px;height:308px;background:var(--white);
    display:flex;align-items:center;justify-content:center;gap:10px;padding:0 16px}
  .brand-dot{width:14px;height:14px;border-radius:50%;background:var(--pink);flex:none}
  .brand-name{font-family:"Fira Sans",sans-serif;font-weight:600;font-size:30px;color:var(--pink);line-height:1.1}

  .contact{position:absolute;left:584px;top:18px;list-style:none;color:var(--white);
    font-family:"Fira Sans Condensed",sans-serif;font-weight:600;font-size:16px}
  .contact li{display:flex;align-items:flex-start;gap:26px;height:32px}
  .contact .icon{width:15px;height:15px;flex:none;margin-top:2px}
  .contact .addr{line-height:1.15;font-size:15px}
  .contact .addr small{font-size:12.5px;display:block}
  .contact-rule{position:absolute;left:560px;top:176px;width:288px;height:12px;background:var(--pink)}

  .program-box{position:absolute;left:410px;top:208px;width:386px;height:220px;background:var(--purple);
    border-radius:6px;text-align:center;color:var(--white);padding-top:20px}
  .program-box .line{font-family:"Chakra Petch",monospace;font-weight:700;font-variant:small-caps;line-height:1.2;white-space:nowrap}
  .program-box .l1{font-size:40px;letter-spacing:5px}
  .program-box .l2{font-size:31px;letter-spacing:1.5px}
  .program-box .l3{font-size:40px;letter-spacing:3px}
  .program-box .note{font-family:"Fira Sans",sans-serif;font-weight:600;font-size:21px;color:var(--ink);margin-top:2px}

  .snap{position:absolute;background:var(--white);padding:8px;box-shadow:0 4px 10px rgba(0,0,0,.25)}
  .snap div{width:100%;height:100%}
  .snap-yoga{left:72px;top:508px;width:246px;height:200px;transform:rotate(-9deg)}
  .snap-yoga div{background:linear-gradient(160deg,#1d1b20,#3b2c46 60%,#2b6f62)}
  .snap-soccer{left:302px;top:494px;width:226px;height:242px;transform:rotate(-5deg)}
  .snap-soccer div{background:linear-gradient(180deg,#9fb7a3 0%,#5f8d50 55%,#d98444 100%)}
  .snap-library{left:526px;top:504px;width:262px;height:236px;transform:rotate(-8deg)}
  .snap-library div{background:linear-gradient(110deg,#d8c9b2,#b8865e 55%,#e3d9cf)}

  .lower-panel{position:absolute;left:0;top:640px;width:848px;height:560px;background:var(--pink)}

  .founder{position:absolute;left:0;top:752px;width:848px;text-align:center;font-family:"Cinzel",serif;
    font-weight:600;font-size:31px;color:var(--ink);line-height:38px;letter-spacing:1.5px}

  .offer-title{position:absolute;left:38px;top:846px;font-family:"Chakra Petch",monospace;font-weight:700;font-variant:small-caps;
    font-size:42px;color:var(--soft-white);letter-spacing:4px}
  .offer-list{position:absolute;left:0;top:896px;width:848px;color:var(--white);font-weight:600;font-size:26px}
  .offer-row{display:flex;gap:24px;height:43px;align-items:center;white-space:nowrap}
  .offer-row span{display:flex;align-items:center;gap:7px}
  .offer-row svg{width:14px;height:14px;flex:none}
  .row1{padding-left:14px}
  .row2{padding-left:44px}
  .row3{padding-left:86px}

  .hours{position:absolute;left:0;width:848px;text-align:center;color:var(--ink);font-family:"Montserrat",sans-serif;font-weight:700}
  .hours-days{top:1050px;font-size:16px}
  .hours-time{top:1092px;font-size:19px;font-variant:small-caps}

  .call-band{position:absolute;left:0;top:1118px}
  .call-number{position:absolute;left:94px;top:1130px;font-family:"Chakra Petch",monospace;font-weight:700;font-size:40px;color:var(--white);letter-spacing:1px}

  .mission{position:absolute;right:0;top:1120px;width:328px;height:80px;background:var(--purple);
    clip-path:polygon(8% 0,100% 0,100% 100%,0 100%);}
  .mission p{position:absolute;right:6px;top:6px;text-align:right;color:var(--white);font-family:"Montserrat",sans-serif;
    font-weight:700;font-size:15px;line-height:24px}
</style>
</head>
<body>
<main class="flyer">
  <div class="header-band"></div>
  <svg class="header-accent" width="848" height="188" viewBox="0 0 848 188" aria-hidden="true">
    <polygon points="0,0 340,0 310,36 0,36" fill="#e667a6"/>
  </svg>

  <div class="hero-photo" role="img" aria-label="Soft background photo of a girl jumping, wearing a crew t-shirt"></div>

  <div class="brand-tile">
    <span class="brand-dot"></span>
    <span class="brand-name">Ridge Lass Crew</span>
  </div>

  <ul class="contact">
    <li>
      <svg class="icon" viewBox="0 0 16 16" aria-hidden="true"><rect x="1" y="3" width="14" height="10" rx="1" fill="#fff"/><polyline points="1,3 8,9 15,3" fill="none" stroke="#b768aa" stroke-width="1.5"/></svg>
      <span>info@ridgelasscrew.example.au</span>
    </li>
    <li>
      <svg class="icon" viewBox="0 0 16 16" aria-hidden="true"><path d="M3 1.5l3 .5 1 3.5-2 1.5c1 2 2.5 3.5 4.5 4.5l1.5-2 3.5 1 .5 3c-7 1.5-13.5-5-12-12z" fill="#fff"/></svg>
      <span>0455817396</span>
    </li>
    <li>
      <svg class="icon" viewBox="0 0 16 16" aria-hidden="true"><circle cx="8" cy="8" r="5" fill="#fff"/></svg>
      <span>http://fb.example/ridgelasscrew</span>
    </li>
    <li>
      <svg class="icon" viewBox="0 0 16 16" aria-hidden="true"><path d="M8 1a5 5 0 0 0-5 5c0 4 5 9 5 9s5-5 5-9a5 5 0 0 0-5-5z" fill="#fff"/><circle cx="8" cy="6" r="2" fill="#b768aa"/></svg>
      <span class="addr">87 Pelham Pde,<br>Larkfield Vale<small>(across from Crestmoor Day Clinic)</small></span>
    </li>
  </ul>
  <div class="contact-rule"></div>

  <section class="program-box">
    <div class="line l1">A Girls Only</div>
    <div class="line l2">After School Program</div>
    <div class="line l3">For 11-14yrs</div>
    <div class="note">as OSHC is no longer available</div>
  </section>

  <div class="lower-panel"></div>

  <figure class="snap snap-yoga"><div role="img" aria-label="Photo of a girl in a yoga side plank pose"></div></figure>
  <figure class="snap snap-soccer"><div role="img" aria-label="Photo of a girl heading a soccer ball on a field"></div></figure>
  <figure class="snap snap-library"><div role="img" aria-label="Photo of a girl studying in a library"></div></figure>

  <h1 class="founder">The Brainchild of Rebecca Folwin<br>Ridge Lass Crew</h1>

  <h2 class="offer-title">We look to offer</h2>
  <div class="offer-list">
    <div class="offer-row row1">
      <span><svg viewBox="0 0 14 14"><circle cx="7" cy="7" r="6" fill="none" stroke="#fff" stroke-width="1.5"/><polyline points="4,7 6.2,9 10,5" fill="none" stroke="#fff" stroke-width="1.5"/></svg>Daily meditation</span>
      <span><svg viewBox="0 0 14 14"><circle cx="7" cy="7" r="6" fill="none" stroke="#fff" stroke-width="1.5"/><polyline points="4,7 6.2,9 10,5" fill="none" stroke="#fff" stroke-width="1.5"/></svg>Healthy snacks</span>
      <span><svg viewBox="0 0 14 14"><circle cx="7" cy="7" r="6" fill="none" stroke="#fff" stroke-width="1.5"/><polyline points="4,7 6.2,9 10,5" fill="none" stroke="#fff" stroke-width="1.5"/></svg>Dedicated homework time</span>
    </div>
    <div class="offer-row row2">
      <span><svg viewBox="0 0 14 14"><circle cx="7" cy="7" r="6" fill="none" stroke="#fff" stroke-width="1.5"/><polyline points="4,7 6.2,9 10,5" fill="none" stroke="#fff" stroke-width="1.5"/></svg>Organised group activity,(yoga, fitness class, soccer etc.)</span>
    </div>
    <div class="offer-row row3">
      <span><svg viewBox="0 0 14 14"><circle cx="7" cy="7" r="6" fill="none" stroke="#fff" stroke-width="1.5"/><polyline points="4,7 6.2,9 10,5" fill="none" stroke="#fff" stroke-width="1.5"/></svg>Regular guests speakers</span>
      <span><svg viewBox="0 0 14 14"><circle cx="7" cy="7" r="6" fill="none" stroke="#fff" stroke-width="1.5"/><polyline points="4,7 6.2,9 10,5" fill="none" stroke="#fff" stroke-width="1.5"/></svg>Social media free zone</span>
    </div>
  </div>

  <p class="hours hours-days">OPEN EVERY AFTERNOON AND DURING SCHOOL HOLIDAYS</p>
  <p class="hours hours-time">3-6pm Monday to Friday</p>

  <svg class="call-band" width="460" height="82" viewBox="0 0 460 82" aria-hidden="true">
    <polygon points="70,6 440,6 400,60 30,60" fill="#9d5494"/>
    <polygon points="56,14 424,14 384,70 16,70" fill="#b768aa"/>
  </svg>
  <p class="call-number">( 0455817396</p>

  <aside class="mission">
    <p>Dedicated to Coaching &amp; Mentoring<br>Our Girls into Strong, Independent<br>Young women</p>
  </aside>
</main>
</body>
</html>
```